sydney wedding photography business needs a business card design

we need a business card design for a sydney based wedding photography and videography business. our business name is :golden hour studio and film. our target clients are 24-35 yrs female. our style is candid, organic, natural, dynamic. we are a team of young photographers and videographers, and help brides to create memories that they will cherish for the rest of their lives. the logo will be provided. we want an elegant design that reflects our style, and also want to give a great impression to our clients that we are one of the best studios in sydney and our brand means quality and premium service.

Target Market(s)

bride to be, 24-35 years old, living in sydney and surrunding areas

Industry/Entity Type

Wedding Photography

Contact Information for Business Card

address: 57 tarrant street, glenmore nsw 2047
mobile: 0431872259
phone: (02) 9163 2408
info@tidewillowstudio.net.au
www.tidewillowstudio.net.au
facebook:tidewillowweddings
instagram:tidewillowweddings

Font styles to use
Serif
Sans Serif

Requirements
Nice to have
• maybe add my slogan"memories beyond eternity" if the layout looks good
Should not have
• no black color, not good idea for wedding biz card

```html
<!DOCTYPE html>
<html lang="en">
<head>
<meta charset="utf-8">
<title>Golden Hour Studio and Film – Business Card</title>
<link rel="stylesheet" href="https://fonts.googleapis.com/css2?family=Arimo:wght@400;700&display=swap">
<style>
  :root {
    --backdrop: #3b3430;
    --card: #f5efe4;
    --card-edge: #e2d8c6;
    --brand-ink: #7a6d62;
    --brand-rule: #b5a898;
    --gold: #c08a17;
    --gold-light: #f0c54a;
    --gold-deep: #a8740b;
    --ink: #4e443c;
    --divider: #cbbfae;
  }
  * { margin: 0; padding: 0; box-sizing: border-box; }
  html, body {
    width: 1200px;
    height: 864px;
    overflow: hidden;
    background: var(--backdrop);
    font-family: "Arimo", Arial, sans-serif;
  }
  .canvas {
    position: relative;
    width: 1200px;
    height: 864px;
  }
  .card {
    position: absolute;
    width: 520px;
    height: 298px;
    background: var(--card);
    border: 1px solid var(--card-edge);
    border-radius: 3px;
    box-shadow: 0 14px 30px rgba(0, 0, 0, 0.45);
  }

  /* Front */
  .card-front {
    left: 50px;
    top: 170px;
    display: flex;
    flex-direction: column;
    align-items: center;
    justify-content: center;
  }
  .studio-name {
    color: var(--brand-ink);
    font-weight: 400;
    font-size: 26px;
    letter-spacing: 1px;
    text-align: center;
    white-space: nowrap;
    line-height: 1.25;
  }
  .social-row {
    display: flex;
    align-items: center;
    gap: 8px;
    margin-top: 26px;
  }
  .social-rule {
    width: 92px;
    height: 1px;
    background: var(--brand-rule);
  }
  .social-dot {
    width: 16px;
    height: 16px;
    border-radius: 50%;
    background: var(--brand-ink);
  }
  .social-handle {
    margin-top: 10px;
    color: var(--brand-ink);
    font-size: 15px;
    letter-spacing: 0.3px;
  }

  /* Back */
  .card-back {
    left: 630px;
    top: 396px;
    display: flex;
    align-items: center;
    padding-left: 44px;
  }
  .emblem {
    width: 150px;
    height: 150px;
    border-radius: 50%;
    background: radial-gradient(circle at 40% 35%, var(--gold-light), var(--gold) 55%, var(--gold-deep));
    flex-shrink: 0;
  }
  .back-divider {
    width: 1px;
    height: 200px;
    margin: 0 22px 0 30px;
    background: linear-gradient(to bottom, transparent, var(--divider) 20%, var(--divider) 80%, transparent);
  }
  .contact {
    color: var(--ink);
    font-size: 14px;
    line-height: 1.25;
  }
  .contact-name {
    color: var(--gold);
    font-weight: 700;
    font-size: 19px;
  }
  .contact-role {
    font-size: 16px;
    margin-bottom: 10px;
  }
  .contact-address { margin-bottom: 8px; }
  .contact-list { list-style: none; }
  .contact-item {
    display: flex;
    align-items: center;
    gap: 7px;
    margin-bottom: 2px;
    white-space: nowrap;
  }
  .contact-icon {
    width: 14px;
    height: 14px;
    flex-shrink: 0;
    fill: var(--gold);
  }
  .contact-icon-line {
    fill: none;
    stroke: var(--gold);
    stroke-width: 1.6;
  }
</style>
</head>
<body>
<main class="canvas">

  <section class="card card-front" aria-label="Card front">
    <p class="studio-name">golden hour studio and film</p>
    <div class="social-row">
      <span class="social-rule"></span>
      <span class="social-dot"></span>
      <span class="social-dot"></span>
      <span class="social-rule"></span>
    </div>
    <p class="social-handle">tidewillowweddings</p>
  </section>

  <section class="card card-back" aria-label="Card back">
    <div class="emblem" role="img" aria-label="Gold studio emblem"></div>
    <span class="back-divider"></span>
    <div class="contact">
      <p class="contact-name">Mara Lindqvist</p>
      <p class="contact-role">President</p>
      <p class="contact-address">57 tarrant street<br>glenmore nsw 2047</p>
      <ul class="contact-list">
        <li class="contact-item">
          <svg class="contact-icon" viewBox="0 0 14 14" aria-hidden="true">
            <path d="M2 5c0-2 2-3 5-3s5 1 5 3l-2 1-1-2H5L4 6z"/>
            <rect x="3" y="7" width="8" height="5" rx="1"/>
          </svg>
          (02) 9163 2408
        </li>
        <li class="contact-item">
          <svg class="contact-icon" viewBox="0 0 14 14" aria-hidden="true">
            <path d="M4 1h6a1 1 0 0 1 1 1v10a1 1 0 0 1-1 1H4a1 1 0 0 1-1-1V2a1 1 0 0 1 1-1zm0 2v8h6V3z"/>
          </svg>
          (04) 3187 2259
        </li>
        <li class="contact-item">
          <svg class="contact-icon" viewBox="0 0 14 14" aria-hidden="true">
            <rect x="1" y="3" width="12" height="8"/>
            <path class="contact-icon-line" d="M1.5 3.5l5.5 4.5 5.5-4.5" stroke="#f5efe4"/>
          </svg>
          info@tidewillowstudio.net.au
        </li>
        <li class="contact-item">
          <svg class="contact-icon" viewBox="0 0 14 14" aria-hidden="true">
            <circle cx="7" cy="7" r="6"/>
          </svg>
          tidewillowstudio.net.au
        </li>
      </ul>
    </div>
  </section>

</main>
</body>
</html>
```